My project benefits Military, First Responders, Police, Fire, and Educators.

Contact Information for Business Card

2 Sided appointment card. Visual side will have my head shot with "Brisk Lantern" in a bold graffic/text. I am picturing maybe the headshot applied to a filter that has a matrix effect where the picture is made up of data/numbers flowing vertically through the photo. I am of course open to other concepts as well. Side two will have contact info presented in an attractive visual complimenting the front.

```html
<!DOCTYPE html>
<html lang="en">
<head>
<meta charset="utf-8">
<title>Brisk Lantern – Appointment Card</title>
<link rel="stylesheet" href="https://fonts.googleapis.com/css2?family=Anton&family=Open+Sans:wght@400;600&display=swap">
<style>
  :root {
    --canvas: #e8e8e8;
    --card: #f7f7f7;
    --ink: #1d1d1d;
    --band: #262626;
    --muted: #3a3a3a;
    --suit: #1f2a44;
    --shirt: #aeb8cc;
  }
  * { box-sizing: border-box; margin: 0; padding: 0; }
  html, body {
    width: 1200px; height: 900px; overflow: hidden;
    background: var(--canvas);
    font-family: "Open Sans", sans-serif;
    color: var(--ink);
  }
  .sheet {
    position: relative; width: 1200px; height: 900px;
  }
  .card {
    position: absolute; left: 285px;
    width: 630px; height: 360px;
    background: var(--card);
    box-shadow: 0 6px 18px rgba(0,0,0,.12);
    overflow: hidden;
  }
  .card--front { top: 60px; }
  .card--back { top: 480px; }

  /* Front */
  .front-band {
    position: absolute; left: 0; right: 0; top: 262px; height: 34px;
    background: var(--band);
  }
  .headshot {
    position: absolute; left: 28px; top: 46px; width: 250px; height: 250px;
    background: linear-gradient(180deg, #d9b79c 0%, #c79a80 35%, var(--shirt) 55%, var(--suit) 72%, var(--suit) 100%);
    border-radius: 120px 120px 0 0;
  }
  .identity {
    position: absolute; left: 320px; top: 92px; width: 290px;
  }
  .brand {
    display: flex; align-items: center; gap: 12px;
    font-family: "Anton", sans-serif; font-size: 36px; letter-spacing: .5px;
    text-transform: uppercase; color: var(--ink); line-height: 1;
  }
  .brand-dot {
    width: 34px; height: 34px; border-radius: 50%; background: var(--ink);
    flex: none;
  }
  .person-name {
    margin-top: 14px;
    font-size: 15px; font-weight: 600; letter-spacing: 1px;
    text-transform: uppercase;
  }
  .person-role { font-size: 13px; color: var(--muted); margin-bottom: 6px; }
  .contact-line {
    display: flex; align-items: center; gap: 8px;
    font-size: 13px; color: var(--muted); line-height: 20px;
  }
  .contact-line svg { width: 12px; height: 12px; fill: var(--ink); flex: none; }

  /* Back */
  .back-band {
    position: absolute; left: 0; right: 0; top: 38px; height: 46px;
    background: var(--band);
  }
  .back-mark {
    position: absolute; left: 50%; top: 31px; width: 60px; height: 60px;
    margin-left: -30px; border-radius: 50%;
    background: var(--ink); border: 4px solid var(--card);
  }
  .appointment {
    position: absolute; left: 0; right: 0; top: 112px; text-align: center;
  }
  .appointment-kicker { font-size: 20px; }
  .appointment-title { font-size: 34px; line-height: 1.1; letter-spacing: .5px; }
  .write-line {
    position: absolute; left: 60px; right: 60px; top: 236px;
    border-top: 1px solid var(--muted);
  }
  .notice {
    position: absolute; left: 0; right: 0; top: 276px; text-align: center;
    font-size: 12px; font-weight: 600; color: var(--ink);
  }
</style>
</head>
<body>
<main class="sheet">

  <section class="card card--front">
    <div class="headshot" role="img" aria-label="Head-and-shoulders portrait of the managing director in a dark suit and tie"></div>
    <div class="front-band"></div>
    <div class="identity">
      <div class="brand"><span class="brand-dot"></span>Brisk Lantern</div>
      <p class="person-name">Marcus Hale</p>
      <p class="person-role">Managing Director</p>
      <p class="contact-line">
        <svg viewBox="0 0 24 24"><path d="M6.6 10.8a15.1 15.1 0 0 0 6.6 6.6l2.2-2.2a1 1 0 0 1 1-.25 11.4 11.4 0 0 0 3.6.57 1 1 0 0 1 1 1V20a1 1 0 0 1-1 1A17 17 0 0 1 3 4a1 1 0 0 1 1-1h3.5a1 1 0 0 1 1 1c0 1.25.2 2.45.57 3.57a1 1 0 0 1-.25 1z"/></svg>
        (044)555014207
      </p>
      <p class="contact-line">
        <svg viewBox="0 0 24 24"><path d="M2 5h20v14H2zm2 2v.5l8 5 8-5V7z"/></svg>
        hello@brisklantern.com
      </p>
      <p class="contact-line">
        <svg viewBox="0 0 24 24"><circle cx="12" cy="12" r="10"/></svg>
        www.brisklantern.com
      </p>
    </div>
  </section>

  <section class="card card--back">
    <div class="back-band"></div>
    <div class="back-mark"></div>
    <div class="appointment">
      <p class="appointment-kicker">Your Next</p>
      <p class="appointment-title">Appointment :</p>
    </div>
    <div class="write-line"></div>
    <p class="notice">Please give 24 hours notice if you need to reschedule your appointment</p>
  </section>

</main>
</body>
</html>
```